Business Card Design

New business card design

Target Market(s)

Residential & Commercial Property Managers

Industry/Entity Type

Plumbing Services

Contact Information for Business Card

Name - Rowan Keddle, title - Director, Phone Number - 0431 286 517, email - rowan@tbk-plumbing.com.au, Company ABN - 73 215 904 386,

Font styles to use
Sans Serif

Colors
0054AA
0677BA
7BADD7
CADEEF
E8F1F8

```html
<!DOCTYPE html>
<html lang="en">
<head>
<meta charset="utf-8">
<title>TBK Plumbing Services – Business Card</title>
<link rel="stylesheet" href="https://fonts.googleapis.com/css2?family=Roboto:wght@300;400;700&display=swap">
<style>
  :root{
    --page:#ececec;
    --card-dark:#1e232b;
    --card-dark-soft:#2a3039;
    --edge-blue:#1a9ee0;
    --accent-blue:#12a3e8;
    --deep-blue:#0677ba;
    --white:#ffffff;
    --text-grey:#55595f;
    --tag-grey:#9aa0a8;
  }
  *{box-sizing:border-box;margin:0;padding:0}
  html,body{width:1200px;height:900px;overflow:hidden;background:var(--page);font-family:"Roboto",Arial,sans-serif}
  .canvas{position:relative;width:1200px;height:900px}

  .card{position:absolute;left:280px;width:640px;height:366px;border-radius:26px;overflow:hidden;
        background:var(--card-dark);border:4px solid var(--edge-blue)}
  .card--front{top:60px}
  .card--back{top:474px}

  .card__wave{position:absolute;inset:0;width:100%;height:100%}

  .brand{position:absolute;color:var(--white);font-weight:300;line-height:1}
  .brand__name{display:flex;align-items:center;gap:10px;letter-spacing:2px}
  .brand__dot{display:inline-block;border-radius:50%;background:var(--accent-blue)}
  .brand__tag{color:var(--tag-grey);font-weight:300;text-transform:lowercase}

  .card--front .brand{left:44px;top:34px}
  .card--front .brand__name{font-size:78px}
  .card--front .brand__dot{width:14px;height:14px}
  .card--front .brand__tag{font-size:11px;letter-spacing:8px;margin-top:8px;padding-left:4px}

  .person{position:absolute;right:34px;top:140px;text-align:right}
  .person__name{color:var(--accent-blue);font-weight:700;font-size:26px;text-transform:uppercase;letter-spacing:.5px}
  .person__role{color:var(--white);font-size:18px;font-weight:400;margin-top:2px}

  .contact{position:absolute;right:70px;top:250px;text-align:right;color:var(--text-grey);font-size:17px;line-height:1.45}
  .contact__abn-label{color:var(--accent-blue)}
  .contact__row{display:flex;justify-content:flex-end;align-items:center;gap:8px}
  .contact__icon{width:14px;height:14px;flex:none}
  .contact__row--abn{margin-bottom:6px;padding-right:22px}

  .card--back .drops{position:absolute;inset:0;background:radial-gradient(ellipse at 70% 70%,var(--card-dark-soft),var(--card-dark) 70%)}
  .card--back .brand{left:0;right:0;top:92px;text-align:center}
  .card--back .brand__name{justify-content:center;font-size:104px}
  .card--back .brand__dot{width:18px;height:18px}
  .card--back .brand__tag{font-size:13px;letter-spacing:10px;margin-top:12px}
</style>
</head>
<body>
<main class="canvas">

  <section class="card card--front" aria-label="Business card front">
    <svg class="card__wave" viewBox="0 0 632 358" preserveAspectRatio="none" aria-hidden="true">
      <path d="M0,156 C120,156 180,226 330,226 C470,226 560,232 632,250 L632,358 L0,358 Z" fill="var(--white)"/>
      <path d="M0,150 C120,150 180,220 330,220 C470,220 560,226 632,244" fill="none" stroke="var(--accent-blue)" stroke-width="9"/>
      <path d="M30,142 C130,146 190,206 340,208 C470,210 560,214 632,230" fill="none" stroke="var(--deep-blue)" stroke-width="2"/>
    </svg>

    <div class="brand">
      <div class="brand__name">tbk <span class="brand__dot"></span></div>
      <div class="brand__tag">plumbing services</div>
    </div>

    <div class="person">
      <div class="person__name">Rowan Keddle</div>
      <div class="person__role">Director</div>
    </div>

    <div class="contact">
      <div class="contact__row contact__row--abn"><span><span class="contact__abn-label">ABN:</span> 73 215 904 386</span></div>
      <div class="contact__row">0431 286 517
        <svg class="contact__icon" viewBox="0 0 14 14" aria-hidden="true"><rect width="14" height="14" rx="3" fill="var(--accent-blue)"/><path d="M4 3.5c0 4 2.5 6.5 6.5 6.5l.5-1.8-2-1-1 1c-1-.5-2-1.5-2.5-2.5l1-1-1-2z" fill="var(--white)"/></svg>
      </div>
      <div class="contact__row">rowan@tbk-plumbing.com.au
        <svg class="contact__icon" viewBox="0 0 14 14" aria-hidden="true"><rect width="14" height="14" rx="3" fill="var(--accent-blue)"/><path d="M3 4.5h8v5H3z M3 4.5l4 3 4-3" fill="none" stroke="var(--white)" stroke-width="1.2"/></svg>
      </div>
    </div>
  </section>

  <section class="card card--back" aria-label="Business card back">
    <div class="drops" role="img" aria-label="Faint pattern of water drops across the card"></div>
    <div class="brand">
      <div class="brand__name">tbk <span class="brand__dot"></span></div>
      <div class="brand__tag">plumbing services</div>
    </div>
  </section>

</main>
</body>
</html>
```